Tallyo Scorecard

Redesign KTR's existing Tallyo scorecard, which tracks and reports key performance indicators (KPIs) for our clients. The scorecard provides our customers with an at-a-glance view of our on-site performance. Tallyo is a tool that automatically populates and reports this data.

Review the attached document and deliver suggested redesign options for the two attached views.
Page 1: Portfolio-wide views (high level rollup of multiple sites)
Page 2: Site-level view
Updates

Project Deadline Extended
Reason: Due to the holiday season within the U.S. around the globe we have decided to extend out deadline in hopes of gaining more participation. We will also be providing comments to the current designs tomorrow.

Font styles to use
Sans Serif

Requirements
Must have
• - Sans serif fonts
- Clean aesthetic
- Utilize the exact key performance indicators as are in the attached mockup
- White background (think Plover-esque)
Nice to have
• - Ideas for animation of design elements
Should not have
• - Pictures (icons are okay)

```html
<!DOCTYPE html>
<html lang="en">
<head>
<meta charset="utf-8">
<title>Tallyo Scorecard – All Sites</title>
<link href="https://fonts.googleapis.com/css2?family=Open+Sans:wght@400;600;700&display=swap" rel="stylesheet">
<style>
  :root{
    --orange:#ee8a00;
    --orange-dark:#b36a12;
    --green:#76a914;
    --green-dark:#4d7812;
    --ink:#4a4a4a;
    --ink-soft:#5b5b5b;
    --band:#ffffff;
    --canvas:#ececec;
    --grid:#cfcfcf;
    --axis:#555555;
  }
  *{box-sizing:border-box;margin:0;padding:0}
  html,body{width:1200px;height:996px;overflow:hidden}
  body{background:var(--canvas);font-family:"Open Sans",Arial,sans-serif;color:var(--ink);position:relative}

  .page-header{position:absolute;left:0;top:0;width:1200px;height:138px;background:linear-gradient(#f2f2f2,#e9e9e9)}
  .page-title{position:absolute;left:282px;top:30px;font-size:44px;font-weight:400;color:var(--orange);line-height:1}
  .page-subtitle{position:absolute;left:282px;top:82px;font-size:25px;color:var(--ink);line-height:1}
  .page-subtitle strong{font-weight:700}
  .brand{position:absolute;right:82px;top:74px;font-size:42px;font-weight:400;color:var(--orange);line-height:1;letter-spacing:-.5px}

  .nav-band{position:absolute;left:0;top:138px;width:1200px;height:240px;background:var(--band);
    box-shadow:inset 0 10px 12px -8px rgba(0,0,0,.25),inset 0 -10px 12px -8px rgba(0,0,0,.25)}
  .category{position:absolute;top:42px;width:140px;margin-left:-70px;text-align:center}
  .category-icon{width:89px;height:89px;border-radius:50%;background:var(--orange);margin:0 auto;display:flex;align-items:center;justify-content:center}
  .category.is-active .category-icon{background:var(--orange-dark)}
  .category-label{display:block;margin-top:10px;font-size:15px;font-weight:700;color:var(--ink-soft)}
  .tab{position:absolute;top:172px;width:134px;height:30px;background:var(--green);color:#fff;font-size:15px;font-weight:700;
    display:flex;align-items:center;justify-content:center;border-radius:1px}
  .tab.is-active{background:var(--green-dark)}

  .scorecard-heading{position:absolute;left:743px;top:406px}
  .section-title{font-size:40px;font-weight:400;color:var(--orange);line-height:1}
  .section-kicker{font-size:20px;font-weight:700;color:var(--ink);margin-top:4px;line-height:1.2}
  .section-note{font-size:22px;color:var(--ink-soft);line-height:1.2}
  .heading-rule{position:absolute;left:736px;top:515px;width:464px;height:3px;background:#777}

  .site-score{position:absolute;left:959px;top:538px}
  .site-score .section-kicker{margin-top:6px}
  .score-dial{position:absolute;left:946px;top:641px;width:96px;height:96px;border-radius:50%;
    background:radial-gradient(circle at 50% 40%,#fafafa 0%,#dcdcdc 60%,#a9a9a9 100%);
    display:flex;align-items:center;justify-content:center;font-size:40px;font-weight:700;color:var(--green)}

  .chart{position:absolute;left:0;top:480px;width:940px;height:390px}
  .legend{position:absolute;left:125px;top:884px;width:805px;font-size:11px;line-height:14.6px;color:var(--ink)}
</style>
</head>
<body>

<header class="page-header">
  <h1 class="page-title">All Sites</h1>
  <p class="page-subtitle"><strong>All Programs</strong> | July 2013</p>
  <div class="brand">KTR Tallyo</div>
</header>

<nav class="nav-band">
  <div class="category is-active" style="left:267px">
    <div class="category-icon">
      <svg width="52" height="40" viewBox="0 0 52 40" fill="none" stroke="#fff" stroke-width="2">
        <rect x="19" y="2" width="14" height="10"/><rect x="2" y="24" width="14" height="10"/><rect x="36" y="24" width="14" height="10"/>
        <path d="M26 13v16M17 29h18" stroke-dasharray="2 2"/>
      </svg>
    </div>
    <span class="category-label">Governance</span>
  </div>
  <div class="category" style="left:405px">
    <div class="category-icon">
      <svg width="50" height="44" viewBox="0 0 50 44" fill="#fff">
        <rect x="8" y="28" width="6" height="12"/><rect x="17" y="22" width="6" height="18"/><rect x="26" y="26" width="6" height="14"/><rect x="35" y="16" width="6" height="24"/>
        <path d="M2 2v40h46" fill="none" stroke="#fff" stroke-width="2"/>
        <path d="M8 20l10-8 8 6 14-12" fill="none" stroke="#fff" stroke-width="2"/>
      </svg>
    </div>
    <span class="category-label">Cost</span>
  </div>
  <div class="category" style="left:544px">
    <div class="category-icon">
      <svg width="44" height="48" viewBox="0 0 44 48" fill="none" stroke="#fff" stroke-width="2">
        <path d="M12 4h20l8 8v32H12z"/><path d="M32 4v8h8"/><path d="M20 20h14M20 26h14M20 32h14"/>
        <circle cx="10" cy="24" r="7" fill="#ee8a00"/><path d="M6 30l-2 10 6-3 6 3-2-10"/>
      </svg>
    </div>
    <span class="category-label">Quality</span>
  </div>
  <div class="category" style="left:682px">
    <div class="category-icon">
      <svg width="44" height="48" viewBox="0 0 44 48" fill="#fff">
        <circle cx="22" cy="14" r="10"/><path d="M4 46c0-12 8-18 18-18s18 6 18 18z"/>
      </svg>
    </div>
    <span class="category-label">EHS</span>
  </div>
  <div class="category" style="left:820px">
    <div class="category-icon">
      <svg width="52" height="44" viewBox="0 0 52 44" fill="#fff">
        <circle cx="12" cy="12" r="6"/><circle cx="40" cy="12" r="6"/><circle cx="26" cy="14" r="8"/>
        <path d="M2 34c0-8 4-12 10-12s8 3 8 3-6 4-6 9zM50 34c0-8-4-12-10-12s-8 3-8 3 6 4 6 9zM12 42c0-10 6-16 14-16s14 6 14 16z"/>
      </svg>
    </div>
    <span class="category-label">Personnel</span>
  </div>
  <div class="category" style="left:959px">
    <div class="category-icon">
      <svg width="44" height="48" viewBox="0 0 44 48" fill="none" stroke="#fff" stroke-width="2">
        <path d="M8 4h22l6 6v34H8z"/><path d="M14 14h16M14 20h16M14 26h10"/>
        <path d="M24 44l14-16 4 4-14 16h-4z" fill="#fff"/>
      </svg>
    </div>
    <span class="category-label">Training</span>
  </div>

  <a class="tab is-active" style="left:219px">Scorecard/KPIs</a>
  <a class="tab" style="left:360px">Updates</a>
  <a class="tab" style="left:500px">Innovations</a>
</nav>

<section class="scorecard-heading">
  <h2 class="section-title">Scorecard</h2>
  <p class="section-kicker">KPI Score By Site</p>
  <p class="section-note">Showing July 2013</p>
</section>
<div class="heading-rule"></div>

<section class="site-score">
  <h2 class="section-title">Site Score</h2>
  <p class="section-kicker">Goal 90%</p>
</section>
<div class="score-dial">86%</div>

<svg class="chart" viewBox="0 0 940 390" role="img" aria-label="KPI score by site bar chart">
  <g stroke="var(--grid)" stroke-width="1" stroke-dasharray="3 2">
    <line x1="127" y1="66" x2="898" y2="66"/><line x1="127" y1="126" x2="898" y2="126"/>
    <line x1="127" y1="186" x2="898" y2="186"/><line x1="127" y1="247" x2="898" y2="247"/>
    <line x1="127" y1="307" x2="898" y2="307"/>
  </g>
  <g font-family="Open Sans, Arial, sans-serif" font-size="18" font-weight="700" fill="var(--ink-soft)" text-anchor="end">
    <text x="115" y="72">100%</text><text x="115" y="132">90%</text><text x="115" y="192">80%</text>
    <text x="115" y="253">70%</text><text x="115" y="313">60%</text><text x="115" y="373">50%</text>
  </g>
  <g>
    <rect x="151" y="66" width="12" height="303" fill="var(--green)"/>
    <rect x="178.2" y="132.2" width="12" height="236.8" fill="var(--orange)"/>
    <rect x="205.4" y="144.3" width="12" height="224.7" fill="var(--green)"/>
    <rect x="232.6" y="66" width="12" height="303" fill="var(--orange)"/>
    <rect x="259.8" y="102.1" width="12" height="266.9" fill="var(--green)"/>
    <rect x="287" y="126.2" width="12" height="242.8" fill="var(--orange)"/>
    <rect x="314.2" y="66" width="12" height="303" fill="var(--green)"/>
    <rect x="341.4" y="126.2" width="12" height="242.8" fill="var(--orange)"/>
    <rect x="368.6" y="144.3" width="12" height="224.7" fill="var(--green)"/>
    <rect x="395.8" y="66" width="12" height="303" fill="var(--orange)"/>
    <rect x="423" y="102.1" width="12" height="266.9" fill="var(--green)"/>
    <rect x="450.2" y="126.2" width="12" height="242.8" fill="var(--orange)"/>
    <rect x="477.4" y="66" width="12" height="303" fill="var(--green)"/>
    <rect x="504.6" y="102.1" width="12" height="266.9" fill="var(--orange)"/>
    <rect x="531.8" y="126.2" width="12" height="242.8" fill="var(--green)"/>
    <rect x="559" y="66" width="12" height="303" fill="var(--orange)"/>
    <rect x="586.2" y="126.2" width="12" height="242.8" fill="var(--green)"/>
    <rect x="613.4" y="147.3" width="12" height="221.7" fill="var(--orange)"/>
    <rect x="640.6" y="66" width="12" height="303" fill="var(--green)"/>
    <rect x="667.8" y="102.1" width="12" height="266.9" fill="var(--orange)"/>
    <rect x="695" y="126.2" width="12" height="242.8" fill="var(--green)"/>
    <rect x="722.2" y="126.2" width="12" height="242.8" fill="var(--orange)"/>
    <rect x="749.4" y="66" width="12" height="303" fill="var(--green)"/>
    <rect x="776.6" y="126.2" width="12" height="242.8" fill="var(--orange)"/>
    <rect x="803.8" y="66" width="12" height="303" fill="var(--green)"/>
    <rect x="831" y="66" width="12" height="303" fill="var(--orange)"/>
    <rect x="858.2" y="102.1" width="12" height="266.9" fill="var(--green)"/>
    <rect x="885.4" y="126.2" width="12" height="242.8" fill="var(--orange)"/>
  </g>
  <line x1="127" y1="24" x2="127" y2="371" stroke="var(--axis)" stroke-width="3"/>
  <line x1="125" y1="369" x2="918" y2="369" stroke="var(--axis)" stroke-width="3"/>
  <g fill="#454545">
    <circle cx="157" cy="369" r="8"/><circle cx="184.2" cy="369" r="8"/><circle cx="211.4" cy="369" r="8"/><circle cx="238.6" cy="369" r="8"/>
    <circle cx="265.8" cy="369" r="8"/><circle cx="293" cy="369" r="8"/><circle cx="320.2" cy="369" r="8"/><circle cx="347.4" cy="369" r="8"/>
    <circle cx="374.6" cy="369" r="8"/><circle cx="401.8" cy="369" r="8"/><circle cx="429" cy="369" r="8"/><circle cx="456.2" cy="369" r="8"/>
    <circle cx="483.4" cy="369" r="8"/><circle cx="510.6" cy="369" r="8"/><circle cx="537.8" cy="369" r="8"/><circle cx="565" cy="369" r="8"/>
    <circle cx="592.2" cy="369" r="8"/><circle cx="619.4" cy="369" r="8"/><circle cx="646.6" cy="369" r="8"/><circle cx="673.8" cy="369" r="8"/>
    <circle cx="701" cy="369" r="8"/><circle cx="728.2" cy="369" r="8"/><circle cx="755.4" cy="369" r="8"/><circle cx="782.6" cy="369" r="8"/>
    <circle cx="809.8" cy="369" r="8"/><circle cx="837" cy="369" r="8"/><circle cx="864.2" cy="369" r="8"/><circle cx="891.4" cy="369" r="8"/>
  </g>
  <g font-family="Open Sans, Arial, sans-serif" font-size="8.5" font-weight="600" fill="#fff" text-anchor="middle">
    <text x="157" y="372">1</text><text x="184.2" y="372">2</text><text x="211.4" y="372">3</text><text x="238.6" y="372">4</text>
    <text x="265.8" y="372">5</text><text x="293" y="372">6</text><text x="320.2" y="372">7</text><text x="347.4" y="372">8</text>
    <text x="374.6" y="372">9</text><text x="401.8" y="372">10</text><text x="429" y="372">11</text><text x="456.2" y="372">12</text>
    <text x="483.4" y="372">13</text><text x="510.6" y="372">14</text><text x="537.8" y="372">15</text><text x="565" y="372">16</text>
    <text x="592.2" y="372">17</text><text x="619.4" y="372">18</text><text x="646.6" y="372">19</text><text x="673.8" y="372">20</text>
    <text x="701" y="372">21</text><text x="728.2" y="372">22</text><text x="755.4" y="372">23</text><text x="782.6" y="372">24</text>
    <text x="809.8" y="372">25</text><text x="837" y="372">26</text><text x="864.2" y="372">27</text><text x="891.4" y="372">28</text>
  </g>
</svg>

<p class="legend">1. Arvenor - Mento Park | 2. Olvex - Vacaville | 3. Kestra - Irvine | 4. Nestling Hub - San Francisco | 5 Brightwell - Irwindale | 6. Corvane - San Jose | 7. Homeline - Skillman | 8. Cardeon - Bridgewater | 9. Arvenor - Mento Park | 10 Olvex - Vacaville | 11 Kestra - Irvine | 12. Nestling Hub - San Francisco | 13 Brightwell - Irwindale | 14. Corvane - San Jose | 15. Homeline - Skillman | 16. Cardeon - Bridgewater | 17. Arvenor - Mento Park | 18. Olvex - Vacaville | 19. Kestra - Irvine | 20. Nestling Hub - San Francisco | 22. Brightwell - Irwindale | 23. Corvane - San Jose | 24. Homeline - Skillman | 25. Cardeon - Bridgewater | 26. Corvane - San Jose | 27. Homeline - Skillman | 28. Cardeon - Bridgewater</p>

</body>
</html>
```